Courses Report - Analytics Redesign

We are a Learning Management System company that is looking to redesign our reporting suite in our product. We would like to add more graphs and visualizations to our reporting help communicate results and give our reporting a more modern look. Screenshots include our current courses report so that you can see the filters and type of data that our users search for. We are using Varno Metrics as our reporting service and please see https://www.varnometrics-demo.net/visual-gallery/ for examples of what type of visualizations can be generated.

Target Market(s)

LMS Administrators, Marketing and Sales Product Trainers

Number of Pages Required

1 page

Font styles to use
Sans Serif

Colors
33b8a4
33a6d7
0392cd
00a990
85cae6
87cfc6
cadf82
abd036
9bcb3b

Requirements
Must have
• Clean and simple look. Use Raleway as font. Easy to use and intuitive filtering. Ability to add/remove filters to the output. Graphical display of results that can drill down.
Nice to have
• Better way of listing other reports in menu on left.
Should not have
• Complicated graphs that cannot be easily understood.

```html
<!DOCTYPE html>
<html lang="en">
<head>
<meta charset="utf-8">
<title>Courses Report</title>
<link href="https://fonts.googleapis.com/css2?family=Raleway:wght@400;500;600&display=swap" rel="stylesheet">
<style>
:root{
  --ink:#1f2d3a;
  --muted:#8a9499;
  --page:#f3f5f7;
  --card:#ffffff;
  --line:#e4e9eb;
  --green:#9bcb3b;
  --green-soft:#cadf82;
  --teal-soft:#87cfc6;
  --blue:#1fb5d6;
  --table-head:#d8e2e4;
}
*{box-sizing:border-box;margin:0;padding:0}
html,body{width:1200px;height:799px;overflow:hidden}
body{font-family:'Raleway',sans-serif;background:var(--page);color:var(--ink);position:relative}
.topbar{position:absolute;left:0;top:0;width:1200px;height:56px;background:#fff;border-bottom:1px solid var(--line)}
.brand{position:absolute;left:50px;top:16px;display:flex;align-items:center;gap:8px;font-size:16px;font-weight:600;color:#2d4a3a}
.brand-dot{width:22px;height:22px;border-radius:50%;background:var(--green)}
.nav a,.subnav a{position:absolute;font-size:11px;color:var(--muted);text-decoration:none;white-space:nowrap}
.nav a{top:21px}
.nav a.active,.subnav a.active{color:var(--ink);font-weight:500}
.nav a.active::after,.subnav a.active::after{content:"";position:absolute;left:0;right:0;bottom:-6px;height:2px;background:var(--blue)}
.user{position:absolute;left:1022px;top:14px;display:flex;align-items:center;gap:8px;font-size:11px}
.avatar{width:28px;height:28px;border-radius:50%;background:#e5f1d0;color:var(--green);font-size:15px;font-weight:500;display:flex;align-items:center;justify-content:center}
.caret{color:var(--muted);font-size:9px;margin-left:2px}
.subbar{position:absolute;left:0;top:56px;width:1200px;height:56px;background:#fff}
.subnav a{top:24px}
.page-title{position:absolute;left:50px;top:144px;font-size:19px;font-weight:400}
.btn{position:absolute;top:142px;height:29px;border-radius:3px;font-size:11px;font-weight:500;display:flex;align-items:center;justify-content:center;gap:6px}
.btn-filter{left:969px;width:83px;background:var(--green);color:#fff}
.btn-results{left:1060px;width:90px;border:1.5px solid var(--green);color:var(--green);background:#fff}
.card{position:absolute;top:186px;height:256px;background:var(--card)}
.card svg{display:block}
.card-learners{left:50px;width:350px}
.card-completed{left:425px;width:725px}
.results{position:absolute;left:50px;top:467px;width:1100px;border-collapse:collapse;font-size:10.5px}
.results th{background:var(--table-head);height:31px;text-align:left;font-weight:600;font-size:9.5px}
.results td{height:37.5px;color:#3a4650;white-space:nowrap}
.results tbody tr:nth-child(odd){background:#fff}
.results th:first-child,.results td:first-child{padding-left:19px;width:59px}
.box{display:inline-block;width:15px;height:15px;border:1px solid #b8c3c7;border-radius:2px;background:#fff;vertical-align:middle}
.pager{position:absolute;left:50px;top:741px;font-size:10px;color:#3a4650}
</style>
</head>
<body>
<header class="topbar">
  <div class="brand"><span class="brand-dot"></span>Learnwell Hub</div>
  <nav class="nav">
    <a style="left:343px">Home</a>
    <a style="left:406px">Users</a>
    <a class="active" style="left:467px">Reports</a>
    <a style="left:537px">Content</a>
    <a style="left:609px">Site</a>
  </nav>
  <div class="user"><span class="avatar">D</span>Dana Whitlow<span class="caret">&#8964;</span></div>
</header>
<div class="subbar">
  <nav class="subnav">
    <a style="left:343px">Saved Reports</a>
    <a style="left:446px">Users</a>
    <a class="active" style="left:506px">Courses</a>
    <a style="left:578px">Due Dates</a>
    <a style="left:661px">Classroom Enrollment</a>
    <a style="left:798px">Course Survey</a>
    <a style="left:899px">Satisfaction Survey</a>
    <a style="left:1022px">Purchase History</a>
  </nav>
</div>

<h1 class="page-title">Courses</h1>
<div class="btn btn-filter">
  <svg width="13" height="11" viewBox="0 0 13 11" fill="none" stroke="#fff" stroke-width="1.2"><line x1="0" y1="2" x2="13" y2="2"/><line x1="0" y1="5.5" x2="13" y2="5.5"/><line x1="0" y1="9" x2="13" y2="9"/><circle cx="9" cy="2" r="1.6" fill="#9bcb3b"/><circle cx="4" cy="5.5" r="1.6" fill="#9bcb3b"/><circle cx="8" cy="9" r="1.6" fill="#9bcb3b"/></svg>
  Filter</div>
<div class="btn btn-results">Filter results</div>

<section class="card card-learners">
<svg width="350" height="256" viewBox="62 233 438 320" font-family="Raleway, sans-serif">
  <text x="86" y="266" font-size="11" font-weight="600" letter-spacing="1.2" fill="#5a666d">TOP LEARNERS</text>
  <g stroke="#e3e8ea" stroke-dasharray="2 2">
    <line x1="213" y1="295" x2="213" y2="488"/><line x1="264" y1="295" x2="264" y2="488"/><line x1="315" y1="295" x2="315" y2="488"/><line x1="365" y1="295" x2="365" y2="488"/><line x1="415" y1="295" x2="415" y2="488"/><line x1="466" y1="295" x2="466" y2="488"/>
    <line x1="162" y1="295" x2="466" y2="295"/><line x1="162" y1="327" x2="466" y2="327"/><line x1="162" y1="359" x2="466" y2="359"/><line x1="162" y1="392" x2="466" y2="392"/><line x1="162" y1="424" x2="466" y2="424"/><line x1="162" y1="456" x2="466" y2="456"/>
  </g>
  <line x1="162" y1="295" x2="162" y2="488" stroke="#9aa5aa"/>
  <g>
    <rect x="163" y="309" width="290" height="7" fill="var(--green-soft)"/>
    <rect x="163" y="341" width="191" height="7" fill="var(--teal-soft)"/>
    <rect x="163" y="373" width="147" height="7" fill="var(--green-soft)"/>
    <rect x="163" y="405" width="128" height="7" fill="var(--teal-soft)"/>
    <rect x="163" y="437" width="82" height="7" fill="var(--green-soft)"/>
    <rect x="163" y="469" width="34" height="7" fill="var(--teal-soft)"/>
  </g>
  <g font-size="8" fill="#3a4650" text-anchor="end">
    <text x="154" y="315">Owen Harte</text><text x="154" y="347">Ross Delane</text><text x="154" y="379">Marion Tebbutt</text><text x="154" y="411">Julian Prewitt</text><text x="154" y="439">Nora Quill</text><text x="154" y="475">Tessa Pike</text>
  </g>
  <g font-size="8.5" fill="#3a4650" text-anchor="middle">
    <text x="162" y="503">0</text><text x="213" y="503">10</text><text x="264" y="503">20</text><text x="315" y="503">30</text><text x="365" y="503">40</text><text x="415" y="503">50</text><text x="466" y="503">60</text>
  </g>
</svg>
</section>

<section class="card card-completed">
<svg width="725" height="256" viewBox="531 233 906 320" font-family="Raleway, sans-serif">
  <text x="555" y="266" font-size="11" font-weight="600" letter-spacing="1.2" fill="#5a666d">COMPLETED COURSES</text>
  <g stroke="#e3e8ea" stroke-dasharray="2 2">
    <line x1="580" y1="295" x2="1407" y2="295"/><line x1="580" y1="359" x2="1407" y2="359"/><line x1="580" y1="423" x2="1407" y2="423"/>
    <line x1="580" y1="295" x2="580" y2="488"/><line x1="660" y1="295" x2="660" y2="488"/><line x1="728" y1="295" x2="728" y2="488"/><line x1="796" y1="295" x2="796" y2="488"/><line x1="864" y1="295" x2="864" y2="488"/><line x1="932" y1="295" x2="932" y2="488"/><line x1="1000" y1="295" x2="1000" y2="488"/><line x1="1068" y1="295" x2="1068" y2="488"/><line x1="1136" y1="295" x2="1136" y2="488"/><line x1="1204" y1="295" x2="1204" y2="488"/><line x1="1272" y1="295" x2="1272" y2="488"/><line x1="1340" y1="295" x2="1340" y2="488"/><line x1="1407" y1="295" x2="1407" y2="488"/>
  </g>
  <line x1="580" y1="488" x2="1407" y2="488" stroke="#9aa5aa"/>
  <g font-size="9" fill="#3a4650" text-anchor="end">
    <text x="566" y="298">15</text><text x="566" y="362">10</text><text x="566" y="426">5</text><text x="566" y="491">0</text>
  </g>
  <g fill="var(--green-soft)">
    <rect x="609" y="404" width="7" height="84"/><rect x="677" y="434" width="7" height="54"/><rect x="745" y="404" width="7" height="84"/><rect x="813" y="442" width="7" height="46"/><rect x="881" y="428" width="7" height="60"/><rect x="949" y="362" width="7" height="126"/><rect x="1017" y="381" width="7" height="107"/><rect x="1085" y="404" width="7" height="84"/><rect x="1153" y="404" width="7" height="84"/><rect x="1221" y="438" width="7" height="50"/><rect x="1289" y="393" width="7" height="95"/><rect x="1357" y="354" width="7" height="134"/>
  </g>
  <g fill="var(--teal-soft)">
    <rect x="625" y="468" width="7" height="20"/><rect x="693" y="422" width="7" height="66"/><rect x="761" y="442" width="7" height="46"/><rect x="829" y="375" width="7" height="113"/><rect x="897" y="428" width="7" height="60"/><rect x="965" y="468" width="7" height="20"/><rect x="1033" y="453" width="7" height="35"/><rect x="1101" y="442" width="7" height="46"/><rect x="1169" y="479" width="7" height="9"/><rect x="1237" y="471" width="7" height="17"/><rect x="1305" y="475" width="7" height="13"/><rect x="1373" y="485" width="7" height="3"/>
  </g>
  <polyline fill="none" stroke="var(--blue)" stroke-width="1.5" points="620,387 688,427 759,397 823,404 893,377 962,382 1027,417 1097,440 1165,430 1234,401 1301,401 1372,354"/>
  <g fill="var(--blue)">
    <circle cx="620" cy="387" r="3.5"/><circle cx="688" cy="427" r="3.5"/><circle cx="759" cy="397" r="3.5"/><circle cx="823" cy="404" r="3.5"/><circle cx="893" cy="377" r="3.5"/><circle cx="962" cy="382" r="3.5"/><circle cx="1027" cy="417" r="3.5"/><circle cx="1097" cy="440" r="3.5"/><circle cx="1165" cy="430" r="3.5"/><circle cx="1234" cy="401" r="3.5"/><circle cx="1301" cy="401" r="3.5"/><circle cx="1372" cy="354" r="3.5"/>
  </g>
  <g font-size="9" fill="#3a4650" text-anchor="middle">
    <text x="620" y="504">Jan</text><text x="692" y="504">Feb</text><text x="763" y="504">Mar</text><text x="830" y="504">Apr</text><text x="897" y="504">May</text><text x="966" y="504">Jun</text><text x="1034" y="504">July</text><text x="1101" y="504">Aug</text><text x="1170" y="504">Sept</text><text x="1237" y="504">Oct</text><text x="1306" y="504">Nov</text><text x="1373" y="504">Dec</text>
  </g>
  <g font-size="11" fill="#5a666d">
    <line x1="833" y1="532" x2="851" y2="532" stroke="var(--blue)" stroke-width="1.5"/><circle cx="842" cy="532" r="3.5" fill="var(--blue)"/>
    <text x="857" y="536">Completed</text>
    <rect x="949" y="527" width="11" height="10" fill="var(--green-soft)"/><text x="967" y="536">In progress</text>
    <rect x="1059" y="527" width="11" height="10" fill="var(--teal-soft)"/><text x="1077" y="536">Not started</text>
  </g>
</svg>
</section>

<table class="results">
  <thead>
    <tr><th><span class="box"></span></th><th style="width:105px">First name</th><th style="width:117px">Last name</th><th style="width:176px">Email address</th><th style="width:304px">Course name</th><th style="width:115px">User status</th><th style="width:117px">Completion date</th><th>Job role</th></tr>
  </thead>
  <tbody>
    <tr><td><span class="box"></span></td><td>Julian</td><td>Prewitt</td><td>julianp@brightlead.net</td><td>Determining Customer Needs</td><td>Completed</td><td>04/21/2016</td><td>Manager</td></tr>
    <tr><td><span class="box"></span></td><td>Owen</td><td>Harte</td><td>owen.harte@postbox.net</td><td>5 Management Mistakes Blocking Sales Reps from Selling</td><td>Completed</td><td>01/17/2019</td><td>Sales rep</td></tr>
    <tr><td><span class="box"></span></td><td>Tessa</td><td>Pike</td><td>tessa.pike@webpost.net</td><td>PDF -- The LMS Evaluation Checklist</td><td>Completed</td><td>04/21/2016</td><td>Manager</td></tr>
    <tr><td><span class="box"></span></td><td>Nora</td><td>Quill</td><td>noraquill@brightlead.net</td><td>Health and Wellness</td><td>Completed</td><td>01/25/2019</td><td>Sales rep</td></tr>
    <tr><td><span class="box"></span></td><td>Julian</td><td>Prewitt</td><td>julianp@brightlead.net</td><td>Determining Customer Needs</td><td>Completed</td><td>04/21/2016</td><td>Manager</td></tr>
    <tr><td><span class="box"></span></td><td>Ross</td><td>Delane</td><td>ross.delane@postbox.net</td><td>Health and Wellness</td><td>Completed</td><td>10/29/2018</td><td>Manager</td></tr>
  </tbody>
</table>
<p class="pager">Showing page 1 of 1</p>
</body>
</html>
```